Bramblewood Card Company Business Cards

We are a trading card store with Glimmorax, sports and other TCG cards, we need a business card design that encompasses a clean cut, modern style with a retro flare. website is bramblewoodcardco.com for reference. Can utilize a comic book era feel or a more modern outdoor feel to utilize the "Pacific Northwest" elements of tress, mountains, etc.

Industry/Entity Type

Trading cards and collectibles

Contact Information for Business Card

business name, email address, phone number, name, owner job title

Font styles to use
Sans Serif

```html
<!DOCTYPE html>
<html lang="en">
<head>
<meta charset="utf-8">
<title>Bramblewood Card Company – Business Cards</title>
<link rel="stylesheet" href="https://fonts.googleapis.com/css2?family=Open+Sans:wght@400;600;700&display=swap">
<style>
  :root {
    --canvas-bg: #e4e5e6;
    --card-white: #fbfbfb;
    --brand-cyan: #17b4d2;
    --brand-cyan-deep: #0fa6c4;
    --ink-grey: #555a5e;
    --soft-grey: #8a8e91;
    --faint-grey: #e3e3e3;
    --white: #ffffff;
  }
  * { box-sizing: border-box; margin: 0; padding: 0; }
  html, body {
    width: 1200px; height: 873px; overflow: hidden;
    background: var(--canvas-bg);
    font-family: "Open Sans", Arial, sans-serif;
  }
  .sheet {
    position: relative; width: 1200px; height: 873px;
    display: flex; align-items: center; justify-content: center; gap: 40px;
  }
  .card {
    position: relative; width: 540px; height: 308px; overflow: hidden;
    box-shadow: 0 6px 18px rgba(0,0,0,.18);
  }
  .card--front { background: var(--card-white); }
  .card--back { background: var(--brand-cyan); }

  .brand-name {
    position: absolute; display: flex; align-items: center; gap: 10px;
    font-weight: 700; font-size: 17px; line-height: 1.15; letter-spacing: .04em;
    text-transform: uppercase;
  }
  .brand-name__mark { width: 14px; height: 14px; flex: none; }
  .card--front .brand-name { left: 50px; top: 48px; color: var(--ink-grey); }
  .card--front .brand-name__mark { background: var(--brand-cyan); }
  .card--back .brand-name { left: 52px; top: 56px; color: var(--white); }
  .card--back .brand-name__mark { background: var(--white); }

  .scenery { position: absolute; right: 0; }
  .card--front .scenery {
    top: 0; width: 290px; height: 140px;
    background: linear-gradient(200deg, #d6d6d6 0%, #ebebeb 55%, rgba(251,251,251,0) 100%);
  }
  .card--back .scenery {
    bottom: 0; width: 270px; height: 150px;
    background: linear-gradient(200deg, rgba(255,255,255,.95) 0%, rgba(255,255,255,.85) 50%, rgba(255,255,255,.2) 100%);
  }

  .holder { position: absolute; left: 54px; top: 230px; }
  .holder__name { color: var(--brand-cyan); font-weight: 600; font-size: 16px; line-height: 1.2; }
  .holder__title { color: var(--ink-grey); font-size: 12px; line-height: 1.3; }

  .contact { position: absolute; left: 302px; top: 211px; width: 180px; }
  .contact__rule { height: 1.5px; background: var(--brand-cyan); margin-bottom: 10px; }
  .contact__list { list-style: none; }
  .contact__item {
    display: flex; align-items: center; gap: 7px;
    color: var(--ink-grey); font-size: 11.5px; line-height: 16px;
  }
  .contact__icon { width: 9px; height: 9px; flex: none; }

  .card--back .web {
    position: absolute; left: 54px; top: 233px;
    color: var(--white); font-size: 11.5px; font-weight: 600;
  }
</style>
</head>
<body>
<main class="sheet">
  <section class="card card--front" aria-label="Business card front">
    <div class="scenery" role="img" aria-label="Faint grey mountain range silhouette"></div>
    <div class="brand-name"><span class="brand-name__mark"></span><span>Bramblewood<br>Card Company</span></div>
    <div class="holder">
      <p class="holder__name">Elias Marlowe</p>
      <p class="holder__title">Managing Director</p>
    </div>
    <div class="contact">
      <div class="contact__rule"></div>
      <ul class="contact__list">
        <li class="contact__item">
          <svg class="contact__icon" viewBox="0 0 10 10" aria-hidden="true"><path d="M2 1l2 2-1 1.2c.6 1.2 1.6 2.2 2.8 2.8L7 6l2 2-1.4 1.4C4.5 9 1 5.5.6 2.4z" fill="#17b4d2"/></svg>
          <span>310.555.0148</span>
        </li>
        <li class="contact__item">
          <svg class="contact__icon" viewBox="0 0 10 10" aria-hidden="true"><rect x=".5" y="2" width="9" height="6.5" fill="#17b4d2"/><path d="M.5 2L5 5.6 9.5 2" stroke="#fff" fill="none"/></svg>
          <span>info@bramblewoodcardco.com</span>
        </li>
        <li class="contact__item">
          <svg class="contact__icon" viewBox="0 0 10 10" aria-hidden="true"><circle cx="5" cy="5" r="4.5" fill="#17b4d2"/><path d="M.5 5h9M5 .5c-2.4 2.6-2.4 6.4 0 9M5 .5c2.4 2.6 2.4 6.4 0 9" stroke="#fff" stroke-width=".7" fill="none"/></svg>
          <span>www.bramblewoodcardco.com</span>
        </li>
      </ul>
    </div>
  </section>

  <section class="card card--back" aria-label="Business card back">
    <div class="scenery" role="img" aria-label="White mountain range silhouette"></div>
    <div class="brand-name"><span class="brand-name__mark"></span><span>Bramblewood<br>Card Company</span></div>
    <p class="web">www.bramblewoodcardco.com</p>
  </section>
</main>
</body>
</html>
```